One of a kind service business!

We are the only ocean freight auditing company in the entire world that does what we do. We provide a innovative service in auditing our clients invoices for billing errors as it relates to the import and export of their products anywhere in the world. We'd like to retain the current logo - but we are open to any interesting concepts that can complete the card.

Target Market(s)

C-Level and Senior Financial executives

Industry/Entity Type

Auditing

Requirements
Must have

• ONE SIDED ONLY
Should not have
• no cartoonish images

```html
<!DOCTYPE html>
<html lang="en">
<head>
<meta charset="utf-8">
<title>Tidemark Review – Business Card</title>
<link rel="stylesheet" href="https://fonts.googleapis.com/css2?family=Arimo:wght@400;700&display=swap">
<style>
  :root {
    --stage: #e6e7ea;
    --card-white: #ffffff;
    --navy: #2b2463;
    --slate: #557a94;
    --ink: #232323;
    --brand-blue: #1f84bd;
  }
  * { margin: 0; padding: 0; box-sizing: border-box; }
  html, body {
    width: 1200px; height: 944px; overflow: hidden;
    background: var(--stage);
    font-family: "Arimo", Arial, sans-serif;
  }
  .business-card {
    position: absolute; left: 100px; top: 186px;
    width: 1000px; height: 573px;
    border-radius: 40px; overflow: hidden;
    background: var(--card-white);
    box-shadow: 0 6px 18px rgba(0,0,0,0.18);
  }
  .card-shapes { position: absolute; inset: 0; width: 1000px; height: 573px; }
  .card-shapes .wave-band { fill: var(--navy); }
  .card-shapes .name-panel { fill: var(--slate); }

  .brand-lockup {
    position: absolute; left: 48px; top: 78px;
    display: flex; align-items: center; gap: 16px;
  }
  .brand-mark { width: 30px; height: 30px; background: var(--brand-blue); }
  .brand-name {
    font-size: 58px; font-weight: 700; color: var(--brand-blue);
    letter-spacing: 1px; line-height: 1;
  }

  .contact-list {
    position: absolute; left: 72px; list-style: none;
    color: var(--ink); font-size: 28px; line-height: 1;
  }
  .contact-list.address { top: 214px; }
  .contact-list.channels { top: 330px; }
  .contact-list li { display: flex; align-items: flex-start; }
  .contact-list.address li + li { margin-top: 5px; }
  .contact-list.channels li + li { margin-top: 6px; }
  .contact-list .icon { width: 24px; height: 24px; margin-right: 16px; flex: none; fill: var(--navy); }
  .contact-list .spacer { width: 40px; flex: none; }

  .person {
    position: absolute; left: 700px; width: 220px; top: 458px;
    text-align: center; color: var(--navy);
  }
  .person-name { font-size: 36px; white-space: nowrap; margin-left: -40px; margin-right: -40px; }
  .person-role { font-size: 22px; margin-top: 8px; }
</style>
</head>
<body>
  <div class="business-card">
    <svg class="card-shapes" viewBox="0 0 1000 573" aria-hidden="true">
      <path class="wave-band" d="M600 0 L1000 0 L1000 573 L490 573 C515 500 545 440 560 370 C580 260 560 150 600 0 Z"/>
      <path class="name-panel" d="M716 0 L1000 0 L1000 573 L605 573 C630 520 640 460 640 380 C640 250 650 130 716 0 Z"/>
    </svg>

    <div class="brand-lockup">
      <span class="brand-mark"></span>
      <span class="brand-name">Tidemark Review</span>
    </div>

    <ul class="contact-list address">
      <li>
        <svg class="icon" viewBox="0 0 24 24" aria-hidden="true"><path d="M12 2 1 12h3v10h6v-6h4v6h6V12h3z"/></svg>
        Vltava Business Park
      </li>
      <li><span class="spacer"></span>Lodní 18, Prague</li>
      <li><span class="spacer"></span>Czech Republic 17000</li>
    </ul>

    <ul class="contact-list channels">
      <li>
        <svg class="icon" viewBox="0 0 24 24" aria-hidden="true"><path d="M8 2c-3 1-5 4-5 8 0 6 5 12 11 12 2 0 3-1 4-2l-3-4-3 1c-2-2-3-5-3-8l3-1-1-5z"/></svg>
        +420 234 555 018
      </li>
      <li>
        <svg class="icon" viewBox="0 0 24 24" aria-hidden="true"><path d="M7 1h10v22H7zM9 4v12h6V4z"/></svg>
        +420 705 314 927
      </li>
      <li>
        <svg class="icon" viewBox="0 0 24 24" aria-hidden="true"><path d="M8 2c-3 1-5 4-5 8 0 6 5 12 11 12 2 0 3-1 4-2l-3-4-3 1c-2-2-3-5-3-8l3-1-1-5z"/></svg>
        +1 555 208 4471 - USA
      </li>
      <li>
        <svg class="icon" viewBox="0 0 24 24" aria-hidden="true"><path d="M6 2h9l3 3v6H6zM2 12h20v10H2zm4 3v2h12v-2z"/></svg>
        +420 234 555 019
      </li>
      <li>
        <svg class="icon" viewBox="0 0 24 24" aria-hidden="true"><circle cx="12" cy="12" r="11"/></svg>
        www.tidemarkreview.net
      </li>
      <li>
        <svg class="icon" viewBox="0 0 24 24" aria-hidden="true"><path d="M1 9 12 2l11 7v13H1zm3 1 8 6 8-6-8-5z"/></svg>
        danielh@tidemarkreview.net
      </li>
    </ul>

    <div class="person">
      <p class="person-name">Daniel Hartwell</p>
      <p class="person-role">CEO</p>
    </div>
  </div>
</body>
</html>
```